Corporate-Design für Osteopathie-Praxis
Das Corporate Design war sehr gut, Änderungswünsche wurden zügig und exakt umgesetzt. Die Designerin stand auch nach der Siegerehrung immer zur Verfügung und hat weitere kleine Änderungen problemlos vorgenommen. Die Zusammenarbeit war immer angenehm und ist nur zu empfehlen.
Zielgruppe
Wir sind eine neue Osteopathie Praxis mit einem Klientel von Jung bis Alt. Vorwiegend etwas gut situiertere Personen. Es soll daher exklusiv aber auch hip sein, da unser Ziel darin besteht eine sehr moderne und edle Praxis aufzubauen.
Aufgabenstellung
Die Praxis soll den Namen „Lumen“ bekommen. Aus zwei Gründen;
die Praxis befindet sich an der Küste in Kiel. Ich möchte hier eine Verbindung zum Standort schaffen. Zweitens sind in dem Namen „Lumen“ meine Initialen LM sowie die Abkürzung für Osteopathie, ost. , vorhanden. Wenn man diese Ideen in dem Logo wiederfinden könnte, wäre es sehr schön. Die Farben blau, weiß, grau richten sich an den skandinavisch-maritimen Stil dem ich folgen möchte. Ich möchte hierbei aber klassisch (nicht verspielt wie zB mit einem Leuchtturm im Logo), etwas exklusiv und hip sein. Es darf aber auch nicht zu abstrakt sein, sodass auch ältere Kunden den Namen/das Logo lesen können

```html
<!DOCTYPE html>
<html lang="de">
<head>
<meta charset="utf-8">
<title>Lumen – Praxis für Osteopathie · Geschäftsausstattung</title>
<link href="https://fonts.googleapis.com/css2?family=Raleway:wght@300;400;500;700&family=Montserrat:wght@700&display=swap" rel="stylesheet">
<style>
  :root{
    --teal:#3e6c82;
    --blue:#9ab6c6;
    --pale:#c9d9e3;
    --grey:#ececec;
    --paper:#ffffff;
    --text:#5d6a72;
    --shadow:0 6px 14px rgba(0,0,0,.18);
  }
  *{margin:0;padding:0;box-sizing:border-box}
  html,body{width:1200px;height:680px;overflow:hidden;background:#fff}
  body{position:relative;font-family:'Raleway',sans-serif;color:var(--text)}
  .piece{position:absolute;background:var(--paper);box-shadow:var(--shadow);overflow:hidden}
  .wave{position:absolute;left:0;width:100%}
  .brand{display:flex;flex-direction:column;align-items:center;position:absolute}
  .brand-name{font-family:'Raleway',sans-serif;font-weight:400;color:var(--teal);letter-spacing:.08em;line-height:1}
  .brand-tag{font-family:'Montserrat',sans-serif;font-weight:700;color:var(--teal);letter-spacing:.06em;white-space:nowrap;line-height:1}

  /* business card, portrait front */
  .card-front{left:34px;top:37px;width:136px;height:203px;background:var(--pale)}
  .card-front .top{position:absolute;left:0;top:0;width:100%;height:62px;background:var(--paper)}
  .card-front .brand{left:0;width:100%;top:12px}
  .card-front .brand-name{font-size:27px}
  .card-front .brand-tag{font-size:4.6px;margin-top:3px}
  .card-front .person{position:absolute;right:10px;top:90px;text-align:right;color:var(--teal);font-size:9px;line-height:1.35}
  .card-front .contact{position:absolute;right:10px;top:134px;text-align:right;color:var(--teal);font-size:5px;line-height:1.9}
  .card-front .web{position:absolute;right:10px;top:186px;color:var(--teal);font-size:6.2px}

  /* business card, portrait back */
  .card-back{left:34px;top:274px;width:136px;height:210px;background:var(--teal)}
  .card-back .top{position:absolute;left:0;top:0;width:100%;height:62px;background:var(--paper)}
  .card-back .brand{left:0;width:100%;top:18px}
  .card-back .brand-name{font-size:27px}
  .card-back .brand-tag{font-size:4.6px;margin-top:3px}
  .card-back .claim{position:absolute;right:10px;top:90px;text-align:right;color:#fff;font-size:7.3px;line-height:1.6}
  .card-back .claim em{font-weight:700}
  .card-back .appointment{position:absolute;right:10px;top:172px;text-align:right;color:#fff;font-size:4.8px;line-height:1.65}

  /* letterhead common */
  .letter{top:37px;width:318px;height:446px}
  .fold{position:absolute;left:0;top:156px;width:13px;height:1px;background:#b8b8b8}
  .letter .body{position:absolute;left:38px;width:218px;font-size:4.8px;line-height:1.45}
  .letter .subject{top:92px}
  .letter .salute{top:117px;color:var(--blue)}
  .letter .p1{top:133px}
  .letter ul{position:absolute;left:42px;width:214px;top:185px;list-style:none;font-size:4.8px;line-height:1.45}
  .letter li{position:relative;padding-left:6px;margin-bottom:11px}
  .letter li::before{content:"";position:absolute;left:-1px;top:3px;width:3px;height:3px;border-radius:50%;background:var(--blue)}
  .letter .p2{top:259px}
  .letter .sign{position:absolute;font-size:4.8px;line-height:1.5}

  .letter-a{left:207px}
  .letter-a .brand{left:0;width:100%;top:22px}
  .letter-a .brand-name{font-size:21px}
  .letter-a .brand-tag{font-size:3.8px;margin-top:2px}
  .letter-a .body{color:#6a747a}
  .letter-a .sign{right:62px;top:325px;text-align:right}
  .letter-a .sign b{display:block;font-weight:400;color:var(--teal);font-size:6px}
  .letter-a .foot{position:absolute;top:386px;left:0;width:100%;display:flex;justify-content:space-around;padding:0 20px;text-align:center;font-size:4.8px;color:var(--teal);line-height:1.4}
  .letter-a .foot svg{display:block;margin:0 auto 6px;width:9px;height:10px}

  .letter-b{left:847px}
  .letter-b .brand{right:24px;top:28px}
  .letter-b .brand-name{font-size:19px}
  .letter-b .brand-tag{font-size:3.3px;margin-top:2px}
  .letter-b .brand .url{font-size:3.1px;color:var(--teal);margin-top:3px}
  .letter-b .body{color:#a8b2b8;left:53px}
  .letter-b .salute{top:120px}
  .letter-b .subject{top:86px}
  .letter-b .p1{top:137px}
  .letter-b ul{left:57px;top:190px;color:#a8b2b8}
  .letter-b li::before{background:var(--teal)}
  .letter-b .p2{top:263px}
  .letter-b .sign{left:53px;top:328px;color:#c4cbd0}
  .letter-b .sign b{display:block;font-weight:400;color:var(--teal);font-size:6px}
  .letter-b .legal{position:absolute;right:22px;top:401px;text-align:right;font-size:2.6px;line-height:2.5;color:var(--teal)}

  /* business card, landscape */
  .card-info{left:592px;top:99px;width:225px;height:146px}
  .card-info .brand{left:14px;top:22px}
  .card-info .brand-name{font-size:20px}
  .card-info .brand-tag{font-size:3.7px;margin-top:2px}
  .card-info .person{position:absolute;left:25px;top:59px;font-size:5px;font-weight:700;font-variant:small-caps;color:var(--teal);line-height:1.6;letter-spacing:.03em}
  .card-info .person span{font-size:6px}
  .card-info .contact{position:absolute;right:14px;top:80px;text-align:right;font-size:5.8px;color:var(--teal);list-style:none}
  .card-info .contact li{display:flex;align-items:center;justify-content:flex-end;gap:5px;height:13px}
  .card-info .contact svg{width:6px;height:6px;fill:var(--teal)}

  .card-logo{left:592px;top:273px;width:225px;height:145px}
  .card-logo .brand{left:0;width:100%;top:32px}
  .card-logo .brand-name{font-size:46px}
  .card-logo .brand-tag{font-size:7.7px;margin-top:6px}
  .card-logo .web{position:absolute;left:0;width:100%;top:121px;text-align:center;font-size:7.5px;color:var(--blue);letter-spacing:.02em}

  /* envelopes */
  .env{background:#f0f0f0}
  .env .window{position:absolute;border-radius:5px;background:linear-gradient(110deg,#e6e6e6 0 40%,#f6f7f8 40% 70%,#eaeaea 70%);box-shadow:inset 0 0 0 1px #dcdcdc}
  .env-a{left:34px;top:524px;width:245px;height:123px}
  .env-a .brand{right:10px;top:17px}
  .env-a .brand-name{font-size:19px}
  .env-a .brand-tag{font-size:3.4px;margin-top:2px}
  .env-a .window{left:22px;top:61px;width:96px;height:44px}
  .env-b{left:306px;top:503px;width:245px;height:145px}
  .env-b .flap{position:absolute;left:0;top:0;width:100%;height:42px}
  .env-b .web{position:absolute;right:36px;top:102px;font-size:5.5px;color:var(--blue)}
  .env-c{left:648px;top:528px;width:245px;height:123px;background:#ebebeb}
  .env-c .brand{left:30px;top:26px}
  .env-c .brand-name{font-size:19px}
  .env-c .brand-tag{font-size:3.4px;margin-top:2px}
  .env-c .window{left:23px;top:61px;width:96px;height:44px}
  .env-c .web{position:absolute;left:143px;top:89px;font-size:5.5px;color:var(--teal)}
  .env-d{left:920px;top:505px;width:245px;height:148px;background:#ebebeb}
  .env-d .flap{position:absolute;left:0;top:0;width:100%;height:42px}
</style>
</head>
<body>

<!-- Visitenkarte hoch, Vorderseite -->
<section class="piece card-front" aria-label="Visitenkarte Vorderseite">
  <div class="top"></div>
  <svg class="wave" style="top:52px;height:24px" viewBox="0 0 136 24" preserveAspectRatio="none"><path d="M0 4 C40 2 80 20 136 6 L136 14 C80 28 40 10 0 12 Z" fill="var(--teal)"/></svg>
  <div class="brand"><span class="brand-name">LUMEN</span><span class="brand-tag">PRAXIS FÜR OSTEOPATHIE</span></div>
  <p class="person">Dr. med.<br>Vorname Nachname</p>
  <p class="contact">Kiel, Hafenweg 12<br>Telefon: +49 431 / 5550123<br>Mobil: +49 170 / 5550123<br>E-Mail: info@lumen-osteopathie.de</p>
  <p class="web">www.lumen-osteopathie.de</p>
</section>

<!-- Visitenkarte hoch, Rückseite -->
<section class="piece card-back" aria-label="Visitenkarte Rückseite">
  <div class="top"></div>
  <svg class="wave" style="top:54px;height:22px" viewBox="0 0 136 22" preserveAspectRatio="none"><path d="M0 6 C40 2 80 18 136 6 L136 14 C80 24 40 10 0 12 Z" fill="var(--blue)"/></svg>
  <div class="brand"><span class="brand-name">LUMEN</span><span class="brand-tag">PRAXIS FÜR OSTEOPATHIE</span></div>
  <p class="claim">Lassen Sie meine Hände<br>und Ihren Körper<br>ein <em>Gespräch</em> führen!</p>
  <p class="appointment">Terminvereinbarung<br>bitte telefonisch<br>oder per EMail</p>
</section>

<!-- Briefbogen Variante A -->
<section class="piece letter letter-a" aria-label="Briefbogen">
  <div class="fold"></div>
  <div class="brand"><span class="brand-name">LUMEN</span><span class="brand-tag">PRAXIS FÜR OSTEOPATHIE</span></div>
  <p class="body subject">Betreff:</p>
  <p class="body salute">Sehr geehrte/er</p>
  <p class="body p1">Lorem ipsum dolor sit amet, consectetur adipiscing elit. Sed ante tortor, rutrum sit amet diam eu, aliquet malesuada eros. Quisque dignissim tortor non purus fringilla finibus. Pellentesque nec dolor augue. Donec vestibulum magna est, sed maximus arcu accumsan a. Donec lacus nisl, dignissim a tempor sed, euismod faucibus dolor.</p>
  <ul>
    <li>Lorem ipsum dolor sit amet, consectetur adipiscing elit. Sed ante tortor, rutrum sit amet diam eu, aliquet malesuada eros. Quisque dignissim tortor non purus fringilla finibus. Pellentesque nec dolor augue.</li>
    <li>Donec vestibulum magna est, sed maximus arcu accumsan a. Donec lacus nisl, dignissim a tempor sed, euismod faucibus dolor. Vestibulum diam magna, porttitor vel consequat a, ultricies vitae mauris</li>
  </ul>
  <p class="body p2">Lorem ipsum dolor sit amet, consectetur adipiscing elit. Sed ante tortor, rutrum sit amet diam eu, aliquet malesuada eros.<br>Quisque dignissim tortor non purus fringilla finibus. Pellentesque nec dolor augue.<br>Donec vestibulum magna est, sed maximus arcu accumsan a.<br>Donec lacus nisl, dignissim a tempor sed, euismod faucibus dolor. Vestibulum diam magna, porttitor vel consequat a, ultricies vitae mauris</p>
  <p class="sign">Unterschrift<b>dr. med</b></p>
  <div class="foot">
    <div><svg viewBox="0 0 10 12"><path d="M5 0a4 4 0 0 0-4 4c0 3 4 8 4 8s4-5 4-8a4 4 0 0 0-4-4zm0 5.6a1.6 1.6 0 1 1 0-3.2 1.6 1.6 0 0 1 0 3.2z" fill="var(--blue)"/></svg>Kiel<br>Hafenweg 12</div>
    <div><svg viewBox="0 0 10 12"><path d="M2 1l2 0 1 3-1.3 1a6 6 0 0 0 2.3 3l1-1.3 3 1v2c-5 1-9-5-8-8.7z" fill="var(--blue)"/></svg>Telefon: +49 431 / 5550123<br>Mobil: +49 170 / 5550123</div>
    <div><svg viewBox="0 0 12 9"><rect x=".5" y=".5" width="11" height="8" fill="none" stroke="var(--blue)"/><path d="M.5 .5l5.5 5 5.5-5" fill="none" stroke="var(--blue)"/></svg>E-Mail: praxis@lumen-osteopathie.de<br>www.lumen-osteopathie.de</div>
  </div>
  <svg class="wave" style="bottom:0;height:40px" viewBox="0 0 318 40" preserveAspectRatio="none"><path d="M0 30 C90 24 170 34 240 30 C280 28 305 18 318 10 L318 14 C305 24 280 34 240 36 C170 40 90 30 0 36 Z" fill="var(--blue)"/></svg>
</section>

<!-- Visitenkarte quer, Kontaktseite -->
<section class="piece card-info" aria-label="Visitenkarte quer, Kontaktseite">
  <svg class="wave" style="top:0;height:146px" viewBox="0 0 225 146" preserveAspectRatio="none"><path d="M225 22 C180 22 150 45 120 80 C95 108 60 122 0 124 L0 146 L225 146 Z" fill="var(--grey)"/></svg>
  <div class="brand"><span class="brand-name">LUMEN</span><span class="brand-tag">PRAXIS FÜR OSTEOPATHIE</span></div>
  <p class="person">Dr. med.<br><span>Vorname Nachname</span></p>
  <ul class="contact">
    <li>Telefon: +49 431 / 5550123 <svg viewBox="0 0 10 10"><path d="M1 0h2l1 3-1.2 1a6 6 0 0 0 2.7 2.7L6.5 5.5 10 6.5V9C4 10 0 5 1 0z"/></svg></li>
    <li>Mobil: +49 170 / 5550123 <svg viewBox="0 0 10 10" style="opacity:0"><rect width="10" height="10"/></svg></li>
    <li>Kiel, Hafenweg 12 <svg viewBox="0 0 10 12"><path d="M5 0a4 4 0 0 0-4 4c0 3 4 8 4 8s4-5 4-8a4 4 0 0 0-4-4z"/></svg></li>
    <li>E-Mail: info@lumen-osteopathie.de <svg viewBox="0 0 10 8"><rect width="10" height="7"/></svg></li>
    <li>www.lumen-osteopathie.de <svg viewBox="0 0 10 10"><circle cx="5" cy="5" r="4.3" fill="none" stroke="var(--teal)" stroke-width="1.2"/><path d="M1 5h8M5 1v8" stroke="var(--teal)" stroke-width="1"/></svg></li>
  </ul>
</section>

<!-- Visitenkarte quer, Logoseite -->
<section class="piece card-logo" aria-label="Visitenkarte quer, Logoseite">
  <div class="brand"><span class="brand-name">LUMEN</span><span class="brand-tag">PRAXIS FÜR OSTEOPATHIE</span></div>
  <p class="web">www.lumen-osteopathie.de</p>
</section>

<!-- Briefbogen Variante B -->
<section class="piece letter letter-b" aria-label="Briefbogen Variante">
  <div class="fold"></div>
  <div class="brand"><span class="brand-name">LUMEN</span><span class="brand-tag">PRAXIS FÜR OSTEOPATHIE</span><span class="url">www.lumen-osteopathie.de</span></div>
  <p class="body subject" style="color:var(--text)">Betreff:</p>
  <p class="body salute">Sehr geehrte/er</p>
  <p class="body p1">Lorem ipsum dolor sit amet, consectetur adipiscing elit. Sed ante tortor, rutrum sit amet diam eu, aliquet malesuada eros. Quisque dignissim tortor non purus fringilla finibus. Pellentesque nec dolor augue. Donec vestibulum magna est, sed maximus arcu accumsan a. Donec lacus nisl, dignissim a tempor sed, euismod faucibus dolor.</p>
  <ul>
    <li>Lorem ipsum dolor sit amet, consectetur adipiscing elit. Sed ante tortor, rutrum sit amet diam eu, aliquet malesuada eros. Quisque dignissim tortor non purus fringilla finibus. Pellentesque nec dolor augue.</li>
    <li>Donec vestibulum magna est, sed maximus arcu accumsan a. Donec lacus nisl, dignissim a tempor sed, euismod faucibus dolor. Vestibulum diam magna, porttitor vel consequat a, ultricies vitae mauris</li>
  </ul>
  <p class="body p2">Lorem ipsum dolor sit amet, consectetur adipiscing elit. Sed ante tortor, rutrum sit amet diam eu, aliquet malesuada eros.<br>Quisque dignissim tortor non purus fringilla finibus. Pellentesque nec dolor augue.<br>Donec vestibulum magna est, sed maximus arcu accumsan a.<br>Donec lacus nisl, dignissim a tempor sed, euismod faucibus dolor. Vestibulum diam magna, porttitor vel consequat a, ultricies vitae mauris</p>
  <p class="sign">Unterschrift<b>dr.med.</b></p>
  <svg class="wave" style="bottom:0;height:80px" viewBox="0 0 318 80" preserveAspectRatio="none"><path d="M0 70 C80 70 120 50 170 30 C220 10 270 4 318 2 L318 80 L0 80 Z" fill="#f1f1f1"/></svg>
  <p class="legal">Kiel • Hafenweg 12 • Telefon: +49 431 / 5550123<br>Mobil: +49 170 / 5550123 • E-Mail: info@lumen-osteopathie.de<br>Bank: Förde Bank AG • Bankleitzahl: 210 500 00<br>IBAN: DE00 2105 0000 1234 5678 90 • BIC: FOERDEXX<br>USt-Nummer: DE 000000000 • Firmensitz: Kiel</p>
</section>

<!-- Umschlag mit Fenster -->
<section class="piece env env-a" aria-label="Briefumschlag mit Fenster">
  <div class="brand"><span class="brand-name">LUMEN</span><span class="brand-tag">PRAXIS FÜR OSTEOPATHIE</span></div>
  <svg class="wave" style="top:78px;height:22px" viewBox="0 0 245 22" preserveAspectRatio="none"><path d="M110 12 C160 4 200 6 245 10 L245 17 C200 12 160 10 110 20 Z" fill="var(--blue)"/></svg>
  <div class="window"></div>
</section>

<!-- Umschlag Rückseite -->
<section class="piece env env-b" aria-label="Briefumschlag Rückseite">
  <svg class="flap" viewBox="0 0 245 42" preserveAspectRatio="none"><path d="M0 0 H245 L232 20 Q225 28 210 28 H35 Q20 28 13 20 Z" fill="#e4e4e4"/></svg>
  <p class="web">www.lumen-osteopathie.de</p>
  <svg class="wave" style="top:92px;height:40px" viewBox="0 0 245 40" preserveAspectRatio="none"><path d="M0 20 C60 16 110 26 160 24 C200 22 230 10 245 0 L245 8 C230 20 200 32 160 33 C110 34 60 26 0 28 Z" fill="var(--blue)"/></svg>
</section>

<!-- Umschlag mit Fenster, Variante -->
<section class="piece env env-c" aria-label="Briefumschlag mit Fenster, Variante">
  <div class="brand"><span class="brand-name">LUMEN</span><span class="brand-tag">PRAXIS FÜR OSTEOPATHIE</span></div>
  <div class="window"></div>
  <p class="web">www.lumen-osteopathie.de</p>
</section>

<!-- Umschlag Rückseite, Variante -->
<section class="piece env env-d" aria-label="Briefumschlag Rückseite, Variante">
  <svg class="flap" viewBox="0 0 245 42" preserveAspectRatio="none"><path d="M0 0 H245 L232 20 Q225 28 210 28 H35 Q20 28 13 20 Z" fill="#e0e0e0"/></svg>
</section>

</body>
</html>
```